Easy Marinade Labels for Butchery Store

Need a set of labels designed for a Butchery Shop. They will sit in the top left corner of the packets as a triangle (7cm each side). Easy because the only major requirement is the label name and some small text saying "Please ask in store to see spec sheet for ingredients". Extra points for finding a fun way to incorporate the logo and/or images of food (garlic bulbs, chilli, spices ect) to enhance the label. List of Marinade Names below: GarlicPepper Mint & RosemarySatayBBQChilli Plum & GingerSundried Tomato & BasilBuffaloHoney SoyHoi-SinPer PeriSpicy CajunTeriyakiBlack Bean Ive also attached the logo and an example of how the label might sit on a packet of meat. Thanks

Target Market(s)

Butchery Deli Shop Customers

Industry/Entity Type

Food Store

Font styles to use
Serif
Sans Serif
Decorative
Other font styles liked:
• Fun font that isn't a generic Quellbrix Font?

Colors

Designer to choose colors to be used in the design.

Requirements
Must have
• Product Name
• Small text saying "Please ask in store to see spec sheet for ingredients"
Nice to have
• Photos of ingredients that would match that type of marinade - Chilli, Garlic, Spices.
• Fenly Oak Logo - not essential if it doesn't look good on the label / doesn't fit.

```html
<!DOCTYPE html>
<html lang="en">
<head>
<meta charset="utf-8">
<title>Marinade Label – Hoisin Sauce</title>
<link rel="stylesheet" href="https://fonts.googleapis.com/css2?family=Amatic+SC:wght@700&family=Oswald:wght@600;700&display=swap">
<style>
  :root {
    --page-bg: #ffffff;
    --frame-yellow: #f2e521;
    --text-light: #ffffff;
    --text-outline: #111111;
    --produce-red: #b3262a;
    --produce-terracotta: #b8643f;
    --produce-orange: #d9843f;
    --produce-green: #5f8f2b;
    --produce-pale: #e6dcc6;
  }
  html, body {
    margin: 0;
    padding: 0;
    width: 1200px;
    height: 900px;
    overflow: hidden;
    background: var(--page-bg);
  }
  .label-canvas {
    display: block;
    width: 1200px;
    height: 900px;
  }
  .label-frame {
    fill: var(--frame-yellow);
  }
  .label-kicker,
  .label-title,
  .label-notice {
    fill: var(--text-light);
    stroke: var(--text-outline);
    paint-order: stroke fill;
    stroke-linejoin: round;
    text-anchor: middle;
  }
  .label-kicker {
    font-family: "Oswald", sans-serif;
    font-weight: 600;
    font-size: 15px;
    letter-spacing: 2px;
    stroke-width: 2.5px;
  }
  .label-title {
    font-family: "Amatic SC", cursive;
    font-weight: 700;
    font-size: 112px;
    stroke-width: 5px;
  }
  .label-notice {
    font-family: "Oswald", sans-serif;
    font-weight: 700;
    font-size: 23px;
    letter-spacing: 2px;
    stroke-width: 3px;
  }
</style>
</head>
<body>
<svg class="label-canvas" viewBox="0 0 1200 900" xmlns="http://www.w3.org/2000/svg">
  <defs>
    <linearGradient id="produce-tones" x1="0" y1="0" x2="1" y2="0">
      <stop offset="0" stop-color="var(--produce-red)"/>
      <stop offset="0.3" stop-color="var(--produce-red)"/>
      <stop offset="0.45" stop-color="var(--produce-terracotta)"/>
      <stop offset="0.65" stop-color="var(--produce-orange)"/>
      <stop offset="0.8" stop-color="var(--produce-green)"/>
      <stop offset="1" stop-color="#3f6a1c"/>
    </linearGradient>
    <linearGradient id="produce-top" x1="0" y1="0" x2="0" y2="1">
      <stop offset="0" stop-color="var(--produce-pale)" stop-opacity="0.95"/>
      <stop offset="0.4" stop-color="var(--produce-pale)" stop-opacity="0"/>
    </linearGradient>
  </defs>

  <g class="marinade-label">
    <polygon class="label-frame" points="621,170 1100,648 141,648"/>
    <g class="produce-photo" role="img" aria-label="Photo of fresh marinade ingredients: red chillies, sweet potato, garlic, spices and green peppers">
      <polygon points="621,185 1083,641 158,641" fill="url(#produce-tones)"/>
      <polygon points="621,185 1083,641 158,641" fill="url(#produce-top)"/>
    </g>

    <text class="label-kicker" x="620" y="375" textLength="172" lengthAdjust="spacing">MARINATED WITH</text>
    <text class="label-title" x="622" y="477" textLength="246" lengthAdjust="spacingAndGlyphs">HOISIN</text>
    <text class="label-title" x="621" y="566" textLength="232" lengthAdjust="spacingAndGlyphs">SAUCE</text>
    <text class="label-notice" x="621" y="621" textLength="740" lengthAdjust="spacingAndGlyphs">PLEASE ASK IN STORE TO SEE SPEC SHEET FOR INGREDIENTS</text>
  </g>
</svg>
</body>
</html>
```